Retro Label for old fashioned soda

We need a label for soda we are having private labeled for our retro, 1950's ice cream shop www.maplefrostparlor.example I don't want the label to look like something from 2017 with a retro feel, but more like an original (possibly kinda cheesy) label you'd see from the 1950's with some of the old catch lines like "tastes great", "invigorating" or "it is refreshing!" The prominent brand should be the name of our ice cream shop, Maple Frost Parlor. the soda is also pure cane sugar so it might be good to have that on somewhere

Label size is 2.4" wide by 4" tall. Here is an example of some retro labels from findwell. I attached on file to this contest but there are more here: https://www.findwell.example/images?q=retro+soda+label&ref=Kx7Qm2Lp9Vt4Rz8Nw3Hd5Jb6Yc1Fg0TsUaWe2Pv7Xo4Ml9Qn8Bk3Dr6Zh5Cy1Ej0Gu7Ai4Ot2Sf9Lw6Nx8Mb3&w=2560&h=1470#img=Pq7Rt2Vw9Xz4Ab:

The label will be the same for all the flavors with the exception of the flavor name changing somewhere on the label. These are the flavors

Root Beer
Orange
Black Cherry
Lemonade
Raspberry Lime -Rickey
White Birch Beer
Lemon Iced Tea
Vanilla Cream
Orange Cream
Sarsaparilla
Ginger Ale

Industry/Entity Type

Shop

Colors

Designer to choose colors to be used in the design.

Requirements
Must have
• retro feel. authentic old fashioned look

```html
<!DOCTYPE html>
<html lang="en">
<head>
<meta charset="utf-8">
<title>Maple Frost Parlor – Soda Labels</title>
<link rel="stylesheet" href="https://fonts.googleapis.com/css2?family=Alfa+Slab+One&family=Crete+Round&family=Old+Standard+TT&family=Yellowtail&display=swap">
<style>
  :root{
    --backdrop:#98a2a1;
    --paper:#e2d5ae;
    --paper-ray:#cfc49a;
    --navy:#18334a;
    --teal:#5f9c8e;
    --cream-line:#efe9d6;
    --gold:#f0c43a;
    --red:#e2332f;
    --ribbon:#e0504a;
    --lime:#5a8a34;
    --orange:#d4541a;
    --cherry:#ad2227;
  }
  html,body{margin:0;padding:0;overflow:hidden}
  body{width:1200px;height:709px;background:var(--backdrop);position:relative}
  .soda-label{position:absolute;top:90px;width:312px;height:520px;display:block}
  .soda-label--lime{left:102px;--flavor:var(--lime)}
  .soda-label--orange{left:441px;--flavor:var(--orange)}
  .soda-label--cherry{left:780px;--flavor:var(--cherry)}
  .flavor-field{fill:var(--flavor)}
  .tagline{font-family:"Alfa Slab One",serif;font-size:23px;fill:var(--gold);letter-spacing:1px}
  .brand-name{font-family:"Alfa Slab One",serif;font-size:44px;fill:var(--gold)}
  .flavor-name{font-family:"Crete Round",serif;font-size:21px;fill:var(--navy)}
  .cane-sugar{font-family:"Yellowtail",cursive;font-size:28px;fill:var(--red);stroke:#fff;stroke-width:3px;paint-order:stroke}
  .volume{font-family:"Old Standard TT",serif;font-size:23px;fill:var(--navy)}
</style>
</head>
<body>

<svg width="0" height="0" style="position:absolute" aria-hidden="true">
  <defs>
    <clipPath id="upper-field"><rect x="0" y="0" width="358" height="300"/></clipPath>
    <path id="tagline-arc" d="M30 188 Q179 78 328 188"/>
    <symbol id="label-art" viewBox="0 0 358 597">
      <rect width="358" height="597" fill="var(--paper)"/>
      <rect class="sunburst" role="img" aria-label="faded sunburst rays" x="0" y="0" width="358" height="597" fill="var(--paper-ray)" opacity=".35"/>
      <path d="M179 8 L342 100 L342 500 L179 592 L16 500 L16 100 Z" fill="var(--navy)"/>
      <path d="M179 16 L335 104 L335 496 L179 584 L23 496 L23 104 Z" fill="var(--teal)"/>
      <path d="M179 28 L324 110 L324 489 L179 571 L34 489 L34 110 Z" fill="none" stroke="var(--cream-line)" stroke-width="4"/>
      <path class="flavor-field" clip-path="url(#upper-field)" d="M179 38 L314 115 L314 483 L179 560 L44 483 L44 115 Z"/>
      <ellipse cx="176" cy="300" rx="162" ry="64" fill="var(--navy)"/>
      <ellipse cx="160" cy="360" rx="90" ry="40" fill="var(--navy)"/>
      <path d="M8 215 L48 190 L62 250 L30 272 Z" fill="var(--ribbon)"/>
      <path d="M350 215 L310 190 L296 250 L328 272 Z" fill="var(--ribbon)"/>
      <path d="M24 192 Q179 80 334 192" fill="none" stroke="var(--navy)" stroke-width="44"/>
      <rect class="crown" role="img" aria-label="crown emblem" x="148" y="48" width="62" height="34" rx="4" fill="var(--navy)"/>
      <path d="M40 387 L306 387 Q300 427 316 467 L40 467 Q56 427 40 387 Z" fill="var(--gold)" stroke="var(--navy)" stroke-width="4"/>
    </symbol>
  </defs>
</svg>

<svg class="soda-label soda-label--lime" viewBox="0 0 358 597" role="img" aria-label="Maple Frost Parlor soda label, Rasberry Lime">
  <use href="#label-art"/>
  <text class="tagline"><textPath href="#tagline-arc" startOffset="50%" text-anchor="middle">QUENCH YOUR THIRST</textPath></text>
  <text class="brand-name" x="176" y="306" text-anchor="middle">Maple Frost</text>
  <text class="brand-name" x="176" y="362" text-anchor="middle">Parlor</text>
  <text class="flavor-name" x="179" y="434" text-anchor="middle">Rasberry Lime</text>
  <g transform="rotate(-6 179 505)">
    <text class="cane-sugar" x="179" y="497" text-anchor="middle">Made from Pure</text>
    <text class="cane-sugar" x="179" y="527" text-anchor="middle">Cane Sugar</text>
  </g>
  <text class="volume" x="28" y="572">16oz</text>
  <text class="volume" x="344" y="572" text-anchor="end">500ml</text>
</svg>

<svg class="soda-label soda-label--orange" viewBox="0 0 358 597" role="img" aria-label="Maple Frost Parlor soda label, Orange">
  <use href="#label-art"/>
  <text class="tagline"><textPath href="#tagline-arc" startOffset="50%" text-anchor="middle">QUENCH YOUR THIRST</textPath></text>
  <text class="brand-name" x="176" y="306" text-anchor="middle">Maple Frost</text>
  <text class="brand-name" x="176" y="362" text-anchor="middle">Parlor</text>
  <text class="flavor-name" x="179" y="434" text-anchor="middle">Orange</text>
  <g transform="rotate(-6 179 505)">
    <text class="cane-sugar" x="179" y="497" text-anchor="middle">Made from Pure</text>
    <text class="cane-sugar" x="179" y="527" text-anchor="middle">Cane Sugar</text>
  </g>
  <text class="volume" x="28" y="572">16oz</text>
  <text class="volume" x="344" y="572" text-anchor="end">500ml</text>
</svg>

<svg class="soda-label soda-label--cherry" viewBox="0 0 358 597" role="img" aria-label="Maple Frost Parlor soda label, Black Cherry">
  <use href="#label-art"/>
  <text class="tagline"><textPath href="#tagline-arc" startOffset="50%" text-anchor="middle">QUENCH YOUR THIRST</textPath></text>
  <text class="brand-name" x="176" y="306" text-anchor="middle">Maple Frost</text>
  <text class="brand-name" x="176" y="362" text-anchor="middle">Parlor</text>
  <text class="flavor-name" x="179" y="434" text-anchor="middle">Black Cherry</text>
  <g transform="rotate(-6 179 505)">
    <text class="cane-sugar" x="179" y="497" text-anchor="middle">Made from Pure</text>
    <text class="cane-sugar" x="179" y="527" text-anchor="middle">Cane Sugar</text>
  </g>
  <text class="volume" x="28" y="572">16oz</text>
  <text class="volume" x="344" y="572" text-anchor="end">500ml</text>
</svg>

</body>
</html>
```